Timber Crest Construction Needs business card

Hey we are in need of business card designs. I have upload our logo as a guideline, but free feel to run with it or come up with something unique.
Pls have fun with it and be creative. the name says it all!
i will give some directions after i see a few entries..
Updates
Logo source file has been uploaded..
Hey because of the logo is so colourful already.
Can we have a few submissions with less colour.
Also we are looking for clever/hidden/descriptive business card.

```html
<!DOCTYPE html>
<html lang="en">
<head>
<meta charset="utf-8">
<title>Timber Crest Construction – Business Card</title>
<link rel="stylesheet" href="https://fonts.googleapis.com/css2?family=Cinzel:wght@700&family=Arimo:wght@400;700&display=swap">
<style>
  :root {
    --page-bg: #ecebe8;
    --card-white: #ffffff;
    --brick-orange: #f07a1e;
    --brick-orange-deep: #e46c12;
    --ink: #111111;
    --brand-grey: #6f7477;
    --frame-grey: #d6d6d6;
  }
  html, body {
    margin: 0;
    width: 1200px;
    height: 1186px;
    overflow: hidden;
    background: var(--page-bg);
  }
  .sheet {
    position: relative;
    width: 1200px;
    height: 1186px;
  }
  .card {
    position: absolute;
    left: 230px;
    width: 740px;
    height: 430px;
    background: var(--card-white);
    box-shadow: 0 0 0 1px var(--frame-grey);
    overflow: hidden;
  }
  .card--front { top: 90px; }
  .card--back { top: 620px; }

  .card__wave {
    position: absolute;
    inset: 0;
    width: 100%;
    height: 100%;
  }
  .wave-fill { fill: var(--brick-orange); }

  .owner {
    position: absolute;
    left: 34px;
    top: 48px;
    margin: 0;
    font-family: "Cinzel", serif;
    font-weight: 700;
    font-size: 26px;
    line-height: 1.2;
    letter-spacing: 2px;
    color: var(--ink);
  }
  .owner__phone { display: block; letter-spacing: 4px; }

  .brand {
    position: absolute;
    left: 200px;
    top: 200px;
    display: flex;
    align-items: center;
    gap: 14px;
  }
  .brand__mark {
    width: 30px;
    height: 30px;
    background: var(--brand-grey);
  }
  .brand__name {
    margin: 0;
    font-family: "Arimo", sans-serif;
    font-weight: 700;
    font-size: 30px;
    color: var(--brand-grey);
    letter-spacing: 0.5px;
  }

  .contact-line {
    position: absolute;
    left: 250px;
    top: 360px;
    margin: 0;
    font-family: "Cinzel", serif;
    font-weight: 700;
    font-size: 22px;
    letter-spacing: 2px;
    color: var(--ink);
  }

  .card__wall {
    position: absolute;
    inset: 0;
    background: linear-gradient(135deg, var(--brick-orange), var(--brick-orange-deep));
  }
  .card__opening {
    position: absolute;
    left: 150px;
    top: 80px;
    width: 440px;
    height: 270px;
    background: var(--card-white);
    display: flex;
    align-items: center;
    justify-content: center;
  }
  .services {
    margin: 0;
    padding: 0;
    list-style: none;
    text-align: center;
    font-family: "Arimo", sans-serif;
    font-size: 32px;
    line-height: 1.25;
    color: var(--ink);
  }
</style>
</head>
<body>
<main class="sheet">

  <section class="card card--front" aria-label="Business card front">
    <svg class="card__wave" viewBox="0 0 740 430" role="img" aria-label="Orange brick wall rising in a curve across the lower edge">
      <path class="wave-fill" d="M0 355 Q 430 335 740 195 L740 430 L0 430 Z"/>
    </svg>
    <p class="owner">Proprietor Name<span class="owner__phone">00000000</span></p>
    <div class="brand">
      <span class="brand__mark" aria-hidden="true"></span>
      <p class="brand__name">Timber Crest Construction</p>
    </div>
    <p class="contact-line">Email, Address</p>
  </section>

  <section class="card card--back" aria-label="Business card back">
    <div class="card__wall" role="img" aria-label="Orange brick wall with an opening in the middle"></div>
    <div class="card__opening">
      <ul class="services">
        <li>Work Features</li>
        <li>Work specialty</li>
        <li>Contact Details</li>
      </ul>
    </div>
  </section>

</main>
</body>
</html>
```